Quote Cards With KB May 2025 for Instagram

I would like to put these quotes over one of the pictures attached; Instagram (new size: 4:5 (1080 x 1350 pixels) One Quote per picture, and I want the quote to be bold or easy to read as well. I provided a few reference graphics that I really like as examples below. In very small letters at the bottom add @KBHarlowOnline

All of the pictures are attached; you can pick any photo and add one quote to it; but no stock photography

```html
<!DOCTYPE html>
<html lang="en">
<head>
<meta charset="utf-8">
<title>Quote Cards — KB — May 2025</title>
<link rel="stylesheet" href="https://fonts.googleapis.com/css2?family=Inter:wght@400;500;700;800;900&display=swap">
<style>
  :root {
    --board: #45b8ae;
    --magenta: #d5006b;
    --blush: #ffd3ea;
    --rose: #f27dbd;
    --ink: #111111;
    --white: #ffffff;
  }
  * { margin: 0; padding: 0; box-sizing: border-box; }
  html, body { width: 720px; height: 1200px; overflow: hidden; }
  body {
    background: var(--board);
    font-family: "Inter", Arial, sans-serif;
    position: relative;
  }
  .card {
    position: absolute;
    width: 288px;
    height: 360px;
    overflow: hidden;
    box-shadow: 0 6px 14px rgba(0, 0, 0, 0.25);
    background: var(--magenta);
  }
  .card--one   { left: 45px;  top: 32px; }
  .card--two   { left: 370px; top: 32px; }
  .card--three { left: 45px;  top: 420px; }
  .card--four  { left: 370px; top: 420px; }
  .card--five  { left: 45px;  top: 808px; }
  .card--six   { left: 388px; top: 808px; }

  .photo { position: absolute; top: 0; height: 100%; }
  .photo--side { left: 155px; width: 133px; }
  .photo--full { left: 0; width: 100%; }
  .photo--studio  { background: linear-gradient(160deg, #d9d9d6 0%, #9a9a98 45%, #2a2a2c 100%); }
  .photo--kitchen { background: linear-gradient(180deg, #6b4a36 0%, #3d2c22 55%, #1c1716 100%); }
  .photo--garden  { background: linear-gradient(180deg, #b9c2c4 0%, #a5708a 40%, #c9a22a 100%); }
  .photo--loft    { background: linear-gradient(170deg, #f2f1ee 0%, #c9c6c0 50%, #2b2a2b 100%); }
  .photo--hills   { background: linear-gradient(180deg, #d9ecf7 0%, #a4b7a6 50%, #1f1f22 100%); }
  .photo--arena   { background: linear-gradient(180deg, #1c2133 0%, #5a4d44 45%, #b88e3a 100%); }

  .panel { position: absolute; left: 0; top: 0; width: 155px; height: 100%; background: var(--magenta); }

  .handle {
    position: absolute;
    left: 0; width: 100%;
    bottom: 8px;
    text-align: center;
    color: var(--white);
    font-weight: 800;
    font-size: 9.5px;
    letter-spacing: 0.1px;
  }
  .panel .handle { width: 155px; }

  .tag {
    display: inline-block;
    background: var(--blush);
    color: var(--magenta);
    font-weight: 800;
  }

  /* Card one */
  .card--one .tag { position: absolute; left: 14px; top: 31px; font-size: 16px; padding: 2px 6px; line-height: 1.15; }
  .card--one .headline { position: absolute; left: 13px; top: 55px; color: var(--white); font-weight: 900; line-height: 0.92; letter-spacing: -1px; }
  .card--one .headline span { display: block; }
  .card--one .h-sm { font-size: 28px; }
  .card--one .h-md { font-size: 50px; letter-spacing: -1.5px; }
  .card--one .h-lg { font-size: 66px; letter-spacing: -2px; }
  .card--one .sub { position: absolute; left: 0; width: 155px; top: 231px; text-align: center; color: var(--white); font-size: 16px; line-height: 1.1; }
  .band { position: absolute; background: var(--rose); color: var(--white); font-weight: 800; }
  .card--one .band { left: 0; top: 280px; width: 155px; height: 38px; font-size: 20px; line-height: 38px; text-align: center; }

  /* Card two */
  .card--two .quote-box { position: absolute; left: 21px; top: 208px; width: 246px; height: 124px; background: var(--blush); padding: 6px 10px; text-align: center; }
  .card--two .q-sm { display: block; color: var(--magenta); font-weight: 900; font-size: 28px; line-height: 1; letter-spacing: -0.5px; }
  .card--two .q-lg { display: block; color: var(--magenta); font-weight: 900; font-size: 50px; line-height: 0.95; letter-spacing: -1.5px; }
  .card--two .q-body { display: block; margin-top: 6px; color: var(--ink); font-size: 12.5px; line-height: 1.15; text-align: left; }
  .card--two .q-body strong { color: var(--magenta); font-weight: 800; }

  /* Card three */
  .card--three .quote-box { position: absolute; left: 30px; top: 196px; width: 229px; height: 100px; background: var(--blush); text-align: center; padding-top: 10px; }
  .card--three .q-head { display: block; color: var(--magenta); font-weight: 900; font-size: 22px; line-height: 1.1; letter-spacing: -0.3px; }
  .card--three .q-body { display: block; color: var(--ink); font-weight: 500; font-size: 14px; line-height: 1.15; }
  .card--three .fix-band { position: absolute; left: 30px; top: 296px; width: 229px; height: 33px; background: var(--magenta); color: var(--white); font-weight: 900; font-size: 26px; line-height: 33px; text-align: center; letter-spacing: -0.5px; }

  /* Card four */
  .card--four .headline { position: absolute; left: 10px; top: 32px; color: var(--white); font-weight: 900; font-size: 47px; line-height: 1; letter-spacing: -1px; }
  .card--four .headline .underlined { text-decoration: underline; text-decoration-thickness: 4px; text-underline-offset: 6px; }
  .card--four .sub { position: absolute; left: 10px; top: 240px; width: 140px; color: var(--white); font-size: 13px; line-height: 1.3; }
  .card--four .sub strong { font-weight: 800; text-decoration: underline; }

  /* Card five */
  .card--five .headline { position: absolute; left: 12px; top: 14px; color: var(--white); font-weight: 900; font-size: 33px; line-height: 1.05; letter-spacing: -0.5px; }
  .card--five .tag { position: absolute; left: 12px; top: 152px; width: 125px; padding: 2px 8px; font-size: 22px; line-height: 1; font-weight: 900; }
  .card--five .cta { position: absolute; left: 12px; top: 202px; width: 145px; color: var(--white); font-size: 19px; line-height: 1.32; }
  .card--five .cta strong { font-weight: 800; text-decoration: underline; }
  .card--five .cta b { font-weight: 800; }

  /* Card six */
  .card--six .pains { position: absolute; left: 0; width: 100%; top: 194px; text-align: center; color: var(--white); }
  .card--six .pains-head { display: block; font-weight: 900; font-size: 18px; line-height: 1.2; }
  .card--six .pains-body { display: block; font-size: 16px; line-height: 1.3; }
  .card--six .band { left: 0; top: 289px; width: 100%; height: 37px; background: var(--blush); color: var(--magenta); font-weight: 900; font-size: 31px; line-height: 38px; text-align: center; letter-spacing: -0.5px; }
</style>
</head>
<body>

<section class="card card--one">
  <div class="panel">
    <span class="tag">Tired. Moody.</span>
    <h2 class="headline"><span class="h-sm">Stubborn</span><span class="h-md">Belly</span><span class="h-lg">Fat.</span></h2>
    <p class="sub">Your hormones are screaming for help!</p>
    <div class="band">Let’s fix that.</div>
    <p class="handle">@KBHarlowOnline</p>
  </div>
  <div class="photo photo--side photo--studio" role="img" aria-label="Photo of KB in a white crop sweater and black pants, posing in a bright studio"></div>
</section>

<section class="card card--two">
  <div class="photo photo--full photo--kitchen" role="img" aria-label="Photo of KB in a sheer black striped top pointing down, in a warm wood kitchen"></div>
  <div class="quote-box">
    <span class="q-sm">That Stubborn</span>
    <span class="q-lg">Weight?</span>
    <span class="q-body">Your hormones are to blame and you’re not alone; <strong>But there is a fix.</strong></span>
  </div>
  <p class="handle">@KBHarlowOnline</p>
</section>

<section class="card card--three">
  <div class="photo photo--full photo--garden" role="img" aria-label="Photo of KB in a mauve sparkle jumpsuit among sunflowers in a mirrored room"></div>
  <div class="quote-box">
    <span class="q-head">The stubborn<br>belly fat after 40?</span>
    <span class="q-body">It’s not about calories; it’s<br>about your hormones.</span>
  </div>
  <div class="fix-band">Here is the fix!</div>
  <p class="handle">@KBHarlowOnline</p>
</section>

<section class="card card--four">
  <div class="panel">
    <h2 class="headline">Your<br>Belly<br>isn’t<br><span class="underlined">Fat…</span></h2>
    <p class="sub">it’s hormonal. And here’s how to fix it. Comment <strong>HORMONES</strong> if nothing is working.</p>
    <p class="handle">@KBHarlowOnline</p>
  </div>
  <div class="photo photo--side photo--loft" role="img" aria-label="Photo of KB in a sheer black striped top dancing in a bright loft"></div>
</section>

<section class="card card--five">
  <div class="panel">
    <h2 class="headline">Flat<br>Tummy<br>in Your<br>40s?</h2>
    <span class="tag">It’s Still Possible!</span>
    <p class="cta">Comment <strong>BYE BELLY</strong> to get the 10 secrets to a <b>flatter tummy</b></p>
    <p class="handle">@KBHarlowOnline</p>
  </div>
  <div class="photo photo--side photo--hills" role="img" aria-label="Photo of KB smiling in a black top and jeans outdoors above green hills"></div>
</section>

<section class="card card--six">
  <div class="photo photo--full photo--arena" role="img" aria-label="Photo of KB in a bronze sparkle turtleneck standing courtside in a basketball arena"></div>
  <p class="pains">
    <span class="pains-head">Bloating. Muffin Top.<br>Puffy Waistline</span>
    <span class="pains-body">Your body’s screaming<br>for a different kind of fix.</span>
  </p>
  <div class="band">HERE IT IS</div>
  <p class="handle">@KBHarlowOnline</p>
</section>

</body>
</html>
```